Tidal Forge - Crypto Currency Miner Powered by Renewable Energy Website

We Need Web Pages Design for Website for Crypto Currency Miner

Serivices include:
Mining Rig Sales
Housing for Rigs turnkey on renewable energy grid
Cloud Mining term packages
Updates

http://www.vaultrigsurvey.example (Competitors sites)

Target Market(s)

Investers for Mining Rigs and terms for 1,2 or 3 years of Hash rate

Industry/Entity Type

Mining

Number of Pages Required

5+ page

Font styles to use
Sans Serif

Colors
add136
9bcb3c
606060
474747
ffc214
cadf82
fbee3e
876aae
6b449b

Requirements
Must have
• Pictures of Solar, Wind and power Factor Correction units
Nice to have
• e-commerce platform so contract terms can be purchased through website
Should not have
• Heavy construction equipment

```html
<!DOCTYPE html>
<html lang="en">
<head>
<meta charset="utf-8">
<title>Tidal Forge – Bitcoin Mining on Renewable Energy</title>
<link href="https://fonts.googleapis.com/css2?family=Questrial&family=Open+Sans:wght@400;600;700&display=swap" rel="stylesheet">
<style>
:root{
  --yellow:#ffc214;
  --green:#9bcb3c;
  --lime:#cadf82;
  --neon:#add136;
  --grey:#606060;
  --dark-grey:#474747;
  --purple:#6b449b;
  --navy:#0e1c28;
  --white:#ffffff;
  --rule:#dcdcdc;
}
*{margin:0;padding:0;box-sizing:border-box}
html,body{width:678px;height:1200px;overflow:hidden;background:var(--white)}
body{position:relative;font-family:"Open Sans",sans-serif;color:var(--grey)}
.abs{position:absolute}
.heading{font-family:"Questrial",sans-serif}

/* nav */
.topnav{left:0;top:0;width:678px;height:24px;background:var(--yellow)}
.topnav ul{list-style:none;position:absolute;left:90px;top:0;display:flex;height:24px}
.topnav li{font-size:6.6px;color:var(--white);text-transform:uppercase;line-height:24px;padding:0 9px}
.topnav li.active{background:var(--dark-grey)}
.search{left:563px;top:0;width:24px;height:24px;background:var(--dark-grey);display:flex;align-items:center;justify-content:center}

/* hero */
.hero{left:0;top:24px;width:678px;height:340px;background:linear-gradient(160deg,#6c6a48 0%,#5a5a3a 40%,#6f6c4c 70%,#5e5538 100%)}
.brand{left:90px;top:40px;display:flex;align-items:center;gap:6px}
.brand-dot{width:18px;height:18px;border-radius:50%;background:var(--green)}
.brand-name{font-family:"Questrial",sans-serif;font-size:13px;color:var(--white)}
.hero-rule{left:90px;top:84px;width:497px;height:1px;background:rgba(255,255,255,.45)}
.hero-title{left:90px;top:144px;color:var(--white);font-family:"Questrial",sans-serif;font-weight:700}
.hero-title h1{font-size:16.5px;letter-spacing:.2px;font-weight:700}
.hero-title h2{font-size:13.2px;font-weight:700}
.hero-copy{left:90px;top:193px;width:250px;font-size:6.6px;line-height:10.5px;color:var(--white)}
.btn{left:90px;top:246px;width:57px;height:22px;background:var(--yellow);color:var(--dark-grey);font-size:6px;font-weight:600;display:flex;align-items:center;justify-content:center;border-radius:2px}

/* service strip */
.service{top:364px;height:114px;width:226px;color:var(--white)}
.s1{left:0;background:linear-gradient(135deg,#e1b12a,#c99a25)}
.s2{left:226px;width:226px;background:linear-gradient(135deg,#b4d66a,#8fbd56)}
.s3{left:452px;background:linear-gradient(135deg,#f0a41a,#d98d12)}
.num{position:absolute;top:25px;width:32px;height:32px;border:1.6px solid var(--white);border-radius:50%;display:flex;align-items:center;justify-content:center;font-size:15px;font-family:"Questrial",sans-serif}
.svc-text{position:absolute;top:22px}
.svc-text h3{font-family:"Questrial",sans-serif;font-size:10.5px;font-weight:700;line-height:13px;margin-bottom:4px}
.svc-text p{font-size:6.6px;line-height:9.6px}

/* welcome */
.welcome{left:90px;top:497px;width:497px;text-align:center}
.welcome h2{font-family:"Questrial",sans-serif;font-size:16px;color:#111;font-weight:700;margin-bottom:10px}
.welcome p{font-size:6.2px;line-height:10px;color:#8a8a8a;margin-bottom:11px}
.divider{left:90px;top:639px;width:497px;height:1px;background:var(--rule)}
.terms-title{left:90px;top:668px;width:497px;text-align:center;font-family:"Questrial",sans-serif;font-size:11px;font-weight:700;color:#111}

.term{top:702px;width:154px;height:92px;border:1px solid #e4e4e4;border-radius:2px;text-align:center}
.term .yr{margin-top:7px;font-family:"Questrial",sans-serif;font-size:9px;color:var(--dark-grey)}
.term .yr b{font-size:25px;font-weight:400;line-height:25px}
.term .rate{font-size:7px;margin-top:3px}
.term p{font-size:6.2px;line-height:8.6px;color:#8a8a8a;margin:7px 10px 0}
.t1 b,.t1 .rate{color:var(--yellow)}
.t2 b,.t2 .rate{color:var(--neon)}
.t3 b,.t3 .rate{color:var(--purple)}

/* app band */
.app-band{left:0;top:834px;width:678px;height:179px;background:var(--navy)}
.app-panel{left:90px;top:834px;width:204px;height:179px;background:var(--yellow)}
.app-device{left:140px;top:846px;width:104px;height:160px;border-radius:14px;background:linear-gradient(160deg,#4caf50,#1f7a35);transform:rotate(25deg)}
.app-copy{left:320px;top:864px;width:250px}
.app-copy h2{font-family:"Questrial",sans-serif;font-size:16px;color:var(--white);font-weight:700;margin-bottom:11px}
.app-copy p{font-size:6px;line-height:8px;color:var(--neon)}
.app-copy a{display:block;font-size:6px;color:var(--white);text-decoration:underline;margin:6px 0 18px}

/* footer */
.footer{left:0;top:1058px;width:678px;height:142px;background:var(--navy)}
.faq-bar{left:90px;top:1045px;width:497px;height:27px;background:var(--yellow);border-radius:2px;color:var(--white);font-size:9px;font-weight:600;display:flex;align-items:center;justify-content:center}
.foot-col h4{font-family:"Questrial",sans-serif;font-size:11px;color:var(--neon);font-weight:700;display:flex;align-items:center;gap:5px;margin-bottom:6px}
.contact{left:90px;top:1080px;width:160px}
.contact p{font-size:5.6px;line-height:7px;color:var(--neon)}
.mail{display:flex;align-items:center;gap:5px;margin-top:8px;font-size:5.6px;color:var(--neon)}
.socials{display:flex;gap:3px;margin-top:8px}
.socials span{width:15px;height:15px;border-radius:50%;background:var(--white)}
.nav-col{left:316px;top:1080px}
.links{list-style:none}
.links li{font-size:5.6px;line-height:10.5px;color:var(--neon)}
.links li::before{content:"›";margin-right:4px}
.links2{left:434px;top:1097px}
.copyright{left:0;top:1178px;width:678px;border-top:1px solid #1f2d38;padding-top:5px;text-align:center;font-size:5.4px;color:var(--yellow)}
</style>
</head>
<body>

<nav class="topnav abs">
  <ul>
    <li class="active">Home</li><li>About Us</li><li>Services</li><li>Contract Terms</li><li>FAQ</li><li>Contact</li>
  </ul>
</nav>
<div class="search abs">
  <svg width="9" height="9" viewBox="0 0 10 10"><circle cx="4" cy="4" r="3" fill="none" stroke="#fff" stroke-width="1.3"/><line x1="6.3" y1="6.3" x2="9" y2="9" stroke="#fff" stroke-width="1.4"/></svg>
</div>

<section class="hero abs" role="img" aria-label="Wind turbines across a hazy mountain valley with power lines"></section>
<div class="brand abs"><span class="brand-dot"></span><span class="brand-name">Tidal Forge</span></div>
<div class="hero-rule abs"></div>
<div class="hero-title abs">
  <h1>START BITCOIN MINING TODAY!</h1>
  <h2>Join over 1.000.000 people with the world's leading hashpower provider</h2>
</div>
<p class="hero-copy abs">It's super simple - Your mining rigs are already set up and running.<br>As soon as you've set-up your account you can start to earn your first coins from our bitcoin cloud mining service!</p>
<div class="btn abs">READ MORE</div>

<div class="service s1 abs" role="img" aria-label="Solar panel field at sunset">
  <span class="num" style="left:91px">1</span>
  <div class="svc-text" style="left:131px;width:85px"><h3>Mining Rig Sales</h3><p>Lorem ipsum dolor sit amet, consectetur adipiscing elit, sed do eiusmod tempor incididunt ut labore et</p></div>
</div>
<div class="service s2 abs" role="img" aria-label="Green field with energy equipment">
  <span class="num" style="left:18px">2</span>
  <div class="svc-text" style="left:58px;width:110px"><h3>Cloud Mining<br>term packages</h3><p>Lorem ipsum dolor sit amet, consectetur adipiscing elit, sed do eiusmod tempor incididunt ut labore et dolore</p></div>
</div>
<div class="service s3 abs" role="img" aria-label="Power factor correction units in golden light">
  <span class="num" style="left:17px">3</span>
  <div class="svc-text" style="left:57px;width:150px"><h3>Housing for Rigs turnkey on renewable energy grid</h3><p style="width:115px">Lorem ipsum dolor sit amet, consectetur adipiscing elit, sed do eiusmod tempor incididunt ut labore et dolore magna aliqua. Ut enim ad minim</p></div>
</div>

<section class="welcome abs">
  <h2>Welcome To The Tidal Forge &amp; Packages</h2>
  <p>Lorem ipsum dolor sit amet, consectetur adipiscing elit, sed do eiusmod tempor incididunt ut labore et dolore magna aliqua. Ut enim ad minim veniam, quis nostrud exercitation ullamco laboris nisi ut aliquip ex ea commodo consequat. Duis aute irure dolor in reprehenderit in voluptate velit esse cillum dolore eu fugiat nulla pariatur. Excepteur sint occaecat cupidatat non proident, sunt in culpa qui officia deserunt mollit anim id est laborum.Lorem ipsum dolor sit amet, consectetur adipiscing elit, sed do eiusmod tempor incididunt ut labore et dolore magna aliqua.</p>
  <p>Ut enim ad minim veniam, quis nostrud exercitation ullamco laboris nisi ut aliquip ex ea commodo consequat. Duis aute irure dolor in reprehenderit in voluptate velit esse cillum dolore eu fugiat nulla pariatur. Excepteur sint occaecat cupidatat non proident, sunt in culpa qui officia deserunt mollit anim id est laborum.</p>
</section>
<div class="divider abs"></div>
<h3 class="terms-title abs">Mining Rigs Investors &amp; Terms For Hash Rate</h3>

<div class="term t1 abs" style="left:90px"><div class="yr"><b>1</b> Year</div><div class="rate">1 years of Hash rate</div><p>Lorem ipsum dolor sit amet, consectetur adipiscing elit, sed do eiusmod tempor incididunt ut labore et dolore magna aliqua.</p></div>
<div class="term t2 abs" style="left:262px"><div class="yr"><b>2</b> Year</div><div class="rate">2 years of Hash rate</div><p>Lorem ipsum dolor sit amet, consectetur adipiscing elit, sed do eiusmod tempor incididunt ut labore et dolore magna aliqua.</p></div>
<div class="term t3 abs" style="left:433px"><div class="yr"><b>3</b> Year</div><div class="rate">3 years of Hash rate</div><p>Lorem ipsum dolor sit amet, consectetur adipiscing elit, sed do eiusmod tempor incididunt ut labore et dolore magna aliqua.</p></div>

<section class="app-band abs"></section>
<div class="app-panel abs"></div>
<div class="app-device abs" role="img" aria-label="Smartphone showing the mining app start screen"></div>
<div class="app-copy abs">
  <h2>Click &amp; Start Mining</h2>
  <p>Lorem ipsum dolor sit amet, consectetur adipiscing elit, sed do eiusmod tempor incididunt ut labore et dolore magna aliqua. Ut enim ad minim veniam, quis nostrud exercitation ullamco laboris nisi ut aliquip ex ea commodo consequat</p>
  <a>Read More</a>
  <p>Lorem ipsum dolor sit amet, consectetur adipiscing elit, sed do eiusmod tempor incididunt ut labore et dolore magna aliqua. Ut enim ad minim veniam, quis nostrud exercitation ullamco laboris nisi ut aliquip ex ea commodo consequat</p>
  <a>Read More</a>
</div>

<footer class="footer abs"></footer>
<div class="faq-bar abs">Please read the FAQ before emailing us. Most questions are answered there. Email: info@tidalforge.example</div>

<div class="foot-col contact abs">
  <h4><svg width="8" height="11" viewBox="0 0 8 11"><path d="M4 0C1.8 0 0 1.7 0 3.9 0 6.8 4 11 4 11s4-4.2 4-7.1C8 1.7 6.2 0 4 0z" fill="#add136"/><circle cx="4" cy="3.9" r="1.5" fill="#0e1c28"/></svg>Contact Us</h4>
  <p>Lorem ipsum dolor sit amet, consectetur adipiscing elit, sed do eiusmod tempor incididunt ut labore et dolore magna aliqua.<br>Tannery: 001- 555-0142</p>
  <div class="mail"><svg width="11" height="8" viewBox="0 0 11 8"><rect width="11" height="8" fill="#add136"/><path d="M0 0l5.5 4.5L11 0" fill="none" stroke="#0e1c28" stroke-width="1"/></svg>info@tidalforge.example</div>
  <div class="socials"><span></span><span></span><span></span><span></span></div>
</div>

<div class="foot-col nav-col abs">
  <h4>Navigation</h4>
  <ul class="links"><li>Home</li><li>About Us</li><li>Services</li><li>Contrac Terms</li><li>FAQ</li><li>Contact Us</li></ul>
</div>
<ul class="links links2 abs"><li>Terms &amp; Condition</li><li>Privacy Policy</li><li>Help</li><li>FAQ</li></ul>

<div class="copyright abs">Copyrights ©2018 The Tidal Forge, All Rights are Rserved.</div>

</body>
</html>
```